Yard Sign Design for Roofing Contractor

We are looking for a new design for our yard signs used on all jobs we build. We are looking for a way to brand the company and are hoping that this contest can give us a "theme" we can incorporate into out other marketing items such as, vehicle graphics, apparel, etc... I have attached a copy of our logo to be used on the sign, it can be "shadowed" with a color to enhance the look and the sign, but please keep the basic logo design. Attached are some samples of construction colors the boss was thinking of along with a picture of our current yard sign to help give some direction and let you know what info is needed on the sign.The darker construction yellow may work better than the fluorescent yellow, but won't know without visual aid. We are not tied to any particular color as of now, so they do have freedom of design as long as keeping with the construction feel. (Just another thought, potentially a reflective construction tape look would be interesting so signs are visable at night)
Updates

Reason: Meeting with new web designers next week to discuss best option to incorporate into our website.Thank you for the submissions!

Target Market(s)

Want signs to stand out when driving by and visibility in neighborhood where sign is posted for potential referrals

Industry/Entity Type

Contractor

Colors
fbed22
fece3e
f37122

Requirements
Must have
• Information that is on our current signs, image attached. I uploaded a .pdf file showing some options that could work for adding "shading" to our logo if you choose to do so.
• Sign should measure 18" T, 24" W
Nice to have
• Interested is seeing designs using construction tape look, images attached

```html
<!DOCTYPE html>
<html lang="en">
<head>
<meta charset="utf-8">
<title>Tallis Construction – Yard Sign</title>
<link rel="stylesheet" href="https://fonts.googleapis.com/css2?family=Archivo+Black&family=Arimo:wght@700&family=Cinzel:wght@400;900&display=swap">
<style>
  :root {
    --tape-dark: #1e1a12;
    --tape-mid: #4a3c14;
    --safety-yellow: #fbed22;
    --amber: #fece3e;
    --panel-white: #ffffff;
    --ink: #111111;
    --band-black: #0d0d0d;
  }
  html, body {
    margin: 0;
    padding: 0;
    overflow: hidden;
    background: var(--ink);
  }
  .sign {
    position: relative;
    width: 1200px;
    height: 900px;
    overflow: hidden;
  }
  .tape-backdrop {
    position: absolute;
    inset: 0;
    background: linear-gradient(135deg, var(--tape-mid) 0%, var(--tape-dark) 50%, var(--tape-mid) 100%);
  }
  .sign-panel {
    position: absolute;
    left: 55px;
    top: 55px;
    width: 1103px;
    height: 675px;
    background: var(--panel-white);
    overflow: hidden;
  }
  .award-corner {
    position: absolute;
    left: 0;
    top: 0;
    width: 545px;
    height: 295px;
  }
  .award-text {
    position: absolute;
    left: 8px;
    top: 92px;
    width: 360px;
    margin: 0;
    transform: rotate(-32deg);
    transform-origin: center;
    font-family: "Archivo Black", sans-serif;
    font-size: 50px;
    line-height: 50px;
    color: var(--ink);
    text-align: center;
    text-transform: uppercase;
  }
  .accreditation-badge {
    position: absolute;
    left: 929px;
    top: 45px;
    width: 96px;
    height: 156px;
  }
  .website {
    position: absolute;
    left: 0;
    right: 0;
    top: 205px;
    margin: 0;
    font-family: "Arimo", sans-serif;
    font-weight: 700;
    font-size: 44px;
    color: var(--ink);
    text-align: center;
  }
  .company-name {
    position: absolute;
    left: 0;
    right: 0;
    top: 270px;
    margin: 0;
    font-family: "Cinzel", serif;
    font-weight: 900;
    color: var(--ink);
    text-align: center;
    line-height: 1;
  }
  .company-name .name-main {
    display: block;
    font-size: 186px;
    letter-spacing: 4px;
  }
  .company-name .name-sub {
    display: block;
    margin-top: 10px;
    font-size: 96px;
    letter-spacing: 1px;
  }
  .services {
    position: absolute;
    left: 0;
    right: 0;
    top: 598px;
    margin: 0;
    font-family: "Cinzel", serif;
    font-weight: 400;
    font-size: 52px;
    color: var(--ink);
    text-align: center;
    word-spacing: 10px;
  }
  .phone-band {
    position: absolute;
    left: 0;
    top: 730px;
    width: 1200px;
    height: 170px;
    background: var(--band-black);
  }
  .phone {
    margin: 0;
    font-family: "Archivo Black", sans-serif;
    font-size: 150px;
    line-height: 170px;
    color: var(--safety-yellow);
    text-align: center;
    letter-spacing: 4px;
  }
</style>
</head>
<body>
  <main class="sign">
    <div class="tape-backdrop" role="img" aria-label="Black and yellow construction hazard tape background"></div>

    <section class="sign-panel">
      <svg class="award-corner" viewBox="0 0 545 295" aria-hidden="true">
        <polygon points="0,0 545,0 0,295" fill="var(--safety-yellow)"/>
      </svg>
      <p class="award-text">Award<br>Winning!</p>

      <svg class="accreditation-badge" viewBox="0 0 96 156" role="img" aria-label="Accreditation badge">
        <rect x="3" y="3" width="90" height="150" rx="10" fill="var(--panel-white)" stroke="var(--ink)" stroke-width="4"/>
      </svg>

      <p class="website">www.tallisroofing.com</p>

      <h1 class="company-name">
        <span class="name-main">TALLIS</span>
        <span class="name-sub">CONSTRUCTION</span>
      </h1>

      <p class="services">ROOF • SIDING • GUTTERS</p>
    </section>

    <footer class="phone-band">
      <p class="phone">405-555-0142</p>
    </footer>
  </main>
</body>
</html>
```